Business Cards for company that supports physicians that do medical research

Need to create a business card for Qorvel Studies (www.qorvelstudies.example), a company devoted to supporting physicians who conduct medical research. The form of the card should match the message of research and information quest. I have provided the logo of the company as an uploaded file. Designs should be simple and slick aimed at very high end clients.

Target Market(s)

Medical doctors that are also researchers

Industry/Entity Type

Medical

Contact Information for Business Card

Should feature logo and fields for personal info:
Name/title
Phone /email

Font styles to use
Serif
Sans Serif

Requirements
Must have
• Qorvel logo and fields for personal info:
• Name: Bertrand Okonfu
• Title: VP Research and Senior Analyst
• Phone: 555-203-4719
• email: info@qorvelstudies.example
Nice to have
• Interesting cards that I've seen:
• 1- all black/charcoal or very dark background
• 2- Plastic - semi-transparent
• 3- non-standard height-width ratios
• 4- Functional cards -- USB drive incorporated
Should not have
• Too busy; needs to stay very simple

```html
<!DOCTYPE html>
<html lang="en">
<head>
<meta charset="utf-8">
<title>Qorvel Studies — Business Card</title>
<link href="https://fonts.googleapis.com/css2?family=Open+Sans:wght@400;600;700&display=swap" rel="stylesheet">
<style>
  :root {
    --page-bg: #e9e9e6;
    --green-light: #74c763;
    --green: #5cb84b;
    --green-dark: #52ad42;
    --charcoal: #050505;
    --charcoal-soft: #151515;
    --stripe-blue: #1c86c9;
    --white: #ffffff;
    --card-shadow: rgba(0, 0, 0, 0.22);
  }
  * { box-sizing: border-box; margin: 0; padding: 0; }
  html, body {
    width: 1200px;
    height: 900px;
    overflow: hidden;
    background: var(--page-bg);
    font-family: "Open Sans", Arial, sans-serif;
  }
  .canvas {
    position: relative;
    width: 1200px;
    height: 900px;
  }
  .card {
    position: absolute;
    left: 320px;
    width: 560px;
    height: 320px;
    border-radius: 4px;
    overflow: hidden;
    box-shadow: 0 10px 28px var(--card-shadow);
  }
  /* Front face */
  .card--front {
    top: 100px;
    background: linear-gradient(160deg, var(--green-light), var(--green-dark));
    color: var(--white);
    text-align: center;
  }
  .card--front .wordmark {
    position: absolute;
    top: 108px;
    left: 0;
    right: 0;
    font-size: 50px;
    font-weight: 600;
    letter-spacing: 1px;
    color: var(--white);
  }
  .card--front .website {
    position: absolute;
    top: 236px;
    left: 0;
    right: 0;
    font-size: 14px;
    font-weight: 400;
    letter-spacing: 0.3px;
  }
  /* Back face */
  .card--back {
    top: 480px;
    background: linear-gradient(160deg, var(--green-light), var(--green-dark));
    color: var(--white);
  }
  .card--back .dark-panel {
    position: absolute;
    top: 0; left: 0; right: 0;
    height: 178px;
    background: linear-gradient(180deg, var(--charcoal-soft), var(--charcoal));
    border-bottom: 7px solid var(--stripe-blue);
  }
  .card--back .wordmark {
    position: absolute;
    top: 64px;
    left: 0;
    right: 0;
    text-align: center;
    font-size: 46px;
    font-weight: 600;
    letter-spacing: 1px;
    color: var(--green);
  }
  .person {
    position: absolute;
    top: 222px;
    left: 36px;
    width: 270px;
    text-align: center;
  }
  .person .name {
    font-size: 21px;
    font-weight: 700;
    line-height: 1.3;
  }
  .person .title {
    font-size: 15px;
    font-weight: 400;
    line-height: 1.4;
  }
  .contact {
    position: absolute;
    top: 210px;
    left: 332px;
    list-style: none;
    font-size: 14px;
  }
  .contact li {
    display: flex;
    align-items: center;
    gap: 10px;
    height: 30px;
  }
  .contact .icon {
    width: 18px;
    height: 18px;
    flex: none;
  }
</style>
</head>
<body>
<main class="canvas">

  <section class="card card--front" aria-label="Card front">
    <div class="wordmark">Qorvel Studies</div>
    <div class="website">www.qorvelstudies.example</div>
  </section>

  <section class="card card--back" aria-label="Card back">
    <div class="dark-panel">
      <div class="wordmark">Qorvel Studies</div>
    </div>

    <div class="person">
      <div class="name">Bertrand Okonfu</div>
      <div class="title">VP Research and Senior Analyst</div>
    </div>

    <ul class="contact">
      <li>
        <svg class="icon" viewBox="0 0 18 18" aria-hidden="true">
          <rect width="18" height="18" rx="3" fill="#ffffff"/>
          <path d="M5 4.5c.6-.5 1.3-.4 1.6.2l.9 1.6c.3.5.1 1-.3 1.3l-.6.4c.5 1.3 1.5 2.3 2.8 2.9l.4-.6c.3-.4.9-.6 1.3-.3l1.6.9c.6.3.7 1 .2 1.6l-.7.8c-.5.5-1.2.7-1.9.4C7.4 12.7 5.3 10.6 4.3 7.7c-.3-.7-.1-1.4.4-1.9z" fill="#5cb84b"/>
        </svg>
        <span>555-203-4719</span>
      </li>
      <li>
        <svg class="icon" viewBox="0 0 18 18" aria-hidden="true">
          <rect width="18" height="18" rx="3" fill="#ffffff"/>
          <rect x="4" y="5.5" width="10" height="7" rx="1" fill="none" stroke="#5cb84b" stroke-width="1.4"/>
          <path d="M4.3 6l4.7 3.6L13.7 6" fill="none" stroke="#5cb84b" stroke-width="1.4"/>
        </svg>
        <span>info@qorvelstudies.example</span>
      </li>
    </ul>
  </section>

</main>
</body>
</html>
```